Calloway needs a modernized design

We would like a modern update (that can be responsive) to our existing website. Attached are the two existing pages we would like new concepts of - our home page and a page about one of our locations.

Calloway is provides executive offices and virtual office services. Startups, law firms, and financial services are our primary clients. We would like a professional, clean design, leaning towards minimalist. We intend to greatly reduce/eliminate the long paragraphs of text.

Requirements
Must have
• A design that can be responsive
Nice to have
• Large image(s) on home page that rotate.

```html
<!DOCTYPE html>
<html lang="en">
<head>
<meta charset="utf-8">
<title>Calloway Business Centre</title>
<link href="https://fonts.googleapis.com/css2?family=Gentium+Book+Plus:wght@400;700&display=swap" rel="stylesheet">
<style>
:root{
  --navy:#2b3a6c;
  --navy-deep:#22305c;
  --bar:#5b67a6;
  --accent:#6b7fc4;
  --submit:#4b67cf;
  --grey-bg:#f0f0f0;
  --text:#444a5c;
  --muted:#8a8f9c;
  --white:#ffffff;
}
*{box-sizing:border-box;margin:0;padding:0}
html,body{width:1200px;height:3243px;overflow:hidden}
body{position:relative;background:var(--white);font-family:"Gentium Book Plus",Georgia,serif;color:var(--text)}
.abs{position:absolute}

/* top bar */
.top-bar{left:0;top:0;width:1200px;height:39px;background:var(--bar);color:var(--white);font-size:13px}
.top-bar .connect{left:145px;top:11px}
.top-bar .phones{right:145px;top:11px}
.top-bar .phones svg{vertical-align:-2px;margin-right:6px}

/* header */
.site-header{left:0;top:39px;width:1200px;height:91px;background:var(--white)}
.brand{display:flex;align-items:center;gap:10px;color:var(--navy);font-size:24px}
.brand .dot{width:42px;height:42px;border-radius:50%;background:var(--navy)}
.site-header .brand{left:145px;top:24px}
.main-nav{right:145px;top:38px;display:flex;gap:34px;font-size:11px;letter-spacing:.5px;text-transform:uppercase;color:#555}
.main-nav .active{color:var(--navy);border-bottom:2px solid var(--navy);padding-bottom:8px}

/* hero */
.hero{left:0;top:130px;width:1200px;height:616px}
.hero-title{left:150px;top:160px;color:var(--white);font-size:72px;line-height:1}
.hero-sub{left:150px;top:242px;color:var(--white);font-size:38px}
.hero-text{left:150px;top:308px;width:330px;color:#e6e9f5;font-size:12.5px;line-height:1.45}
.btn-learn{left:148px;top:410px;width:108px;height:38px;background:var(--accent);color:var(--white);font-size:12px;display:flex;align-items:center;justify-content:center}
.hero-arrows{left:148px;top:508px}

/* services */
.services{left:0;top:746px;width:1200px;height:674px;background:var(--grey-bg)}
.tile{position:absolute}
.tile .label{position:absolute;left:26px;bottom:26px;background:rgba(34,48,92,.88);color:var(--white);font-size:17px;line-height:1.15;padding:16px 18px 16px 27px}
.tile .label svg{display:block;margin-bottom:8px}

/* provide */
.provide-title{left:0;top:1462px;width:1200px;text-align:center;font-size:30px;color:var(--navy)}
.provide-sub{left:0;top:1512px;width:1200px;text-align:center;font-size:15px;color:#555}
.feature{position:absolute;width:300px;text-align:center}
.feature .circle{width:132px;height:132px;border-radius:50%;background:var(--navy);margin:0 auto;display:flex;align-items:center;justify-content:center}
.feature h3{font-weight:400;font-size:22px;color:var(--navy);margin-top:30px}
.feature p{font-size:11px;line-height:1.6;color:var(--muted);margin-top:26px}

/* value */
.value{left:0;top:1929px;width:1200px;height:460px;background:var(--navy)}
.value h2{position:absolute;left:0;top:94px;width:1200px;text-align:center;font-weight:400;font-size:22px;color:var(--white)}
.value p{position:absolute;left:160px;top:158px;width:880px;text-align:center;font-size:13px;line-height:1.75;color:var(--white)}
.btn-outline{left:543px;top:321px;width:112px;height:40px;border:1.5px solid var(--white);color:var(--white);font-size:12px;display:flex;align-items:center;justify-content:center}
.dots{left:577px;top:406px;display:flex;gap:9px}
.dots span{width:8px;height:8px;border-radius:50%;background:var(--white)}
.dots span:first-child{background:var(--accent)}

/* request form */
.request{left:0;top:2389px;width:1200px;height:560px}
.request h2{position:absolute;left:0;top:50px;width:1200px;text-align:center;font-weight:400;font-size:27px;color:var(--white)}
.field{position:absolute;width:364px}
.field label{display:block;font-size:12.5px;color:var(--white);margin-bottom:10px}
.field .input{height:36px;border:1px solid #c9d0ea;background:rgba(255,255,255,.06);color:#dfe3f2;font-size:9px;padding:12px 12px 0}
.submit{left:545px;top:461px;width:110px;height:38px;background:var(--submit);color:var(--white);font-size:12px;letter-spacing:.5px;display:flex;align-items:center;justify-content:center}

/* footer */
.site-footer{left:0;top:2949px;width:1200px;height:294px;background:var(--white)}
.site-footer .brand{left:145px;top:58px}
.foot-col{position:absolute;top:57px;font-size:12.5px;line-height:24px;color:#555;list-style:none}
.foot-contact{position:absolute;left:845px;top:57px;font-size:12.5px;line-height:24px;color:#555}
.foot-contact span{color:var(--navy);padding:0 8px}
.bottom-bar{left:0;top:3183px;width:1200px;height:60px;border-top:1px solid #e2e2e2;font-size:12.5px;color:#555}
.bottom-bar .copy{left:145px;top:22px}
.bottom-bar .connect{right:145px;top:22px}
</style>
</head>
<body>

<div class="abs top-bar">
  <span class="abs connect">Connect With Us</span>
  <span class="abs phones"><svg width="12" height="12" viewBox="0 0 24 24"><path fill="#fff" d="M6.6 10.8c1.4 2.8 3.8 5.1 6.6 6.6l2.2-2.2c.3-.3.7-.4 1-.2 1.1.4 2.3.6 3.6.6.6 0 1 .4 1 1V20c0 .6-.4 1-1 1C10.6 21 3 13.4 3 4c0-.6.4-1 1-1h3.5c.6 0 1 .4 1 1 0 1.3.2 2.5.6 3.6.1.3 0 .7-.2 1z"/></svg>Dallas 214.555.0140 &nbsp;|&nbsp; Houston 713.555.0182</span>
</div>

<header class="abs site-header">
  <div class="abs brand"><span class="dot"></span>Calloway</div>
  <nav class="abs main-nav">
    <span class="active">Home</span><span>Properties</span><span>Virtual Tours &amp; Videos</span><span>Photos</span><span>Broker Referrals</span>
  </nav>
</header>

<section class="abs hero">
  <svg width="1200" height="616" role="img" aria-label="Businessman in a suit talking on the phone at a laptop in a bright office">
    <defs>
      <linearGradient id="heroPhoto" x1="0" y1="0" x2="1" y2="1">
        <stop offset="0" stop-color="#d9dbe0"/><stop offset=".5" stop-color="#9ea2ab"/><stop offset="1" stop-color="#5c606a"/>
      </linearGradient>
    </defs>
    <rect width="1200" height="616" fill="url(#heroPhoto)"/>
    <polygon points="0,0 588,0 486,616 0,616" fill="#4c5795" opacity=".93"/>
  </svg>
  <div class="abs hero-title">Calloway</div>
  <div class="abs hero-sub">Business Centre</div>
  <p class="abs hero-text">Sed ut perspiciatis unde omnis iste natus error sit voluptatem accusantium doloremque laudantium, totam rem aperiam, eaque ipsa quae ab illo inventore veritatis et quasi architecto</p>
  <div class="abs btn-learn">Learn More</div>
  <svg class="abs hero-arrows" width="40" height="16"><path d="M8 3 3 8l5 5M30 3l5 5-5 5" stroke="#fff" stroke-width="2" fill="none"/></svg>
</section>

<section class="abs services">
  <div class="tile" style="left:145px;top:82px;width:441px;height:247px" role="img" aria-label="Colleagues meeting in an executive office">
    <svg width="441" height="247"><rect width="441" height="247" fill="#7d7a75"/></svg>
    <div class="label"><svg width="24" height="20"><rect x="2" y="6" width="20" height="13" rx="2" fill="#fff"/><rect x="8" y="2" width="8" height="5" fill="none" stroke="#fff" stroke-width="2"/></svg>Executive<br>Office Suites</div>
  </div>
  <div class="tile" style="left:614px;top:82px;width:441px;height:247px" role="img" aria-label="Team gathered around a table in a meeting room">
    <svg width="441" height="247"><rect width="441" height="247" fill="#5f5d62"/></svg>
    <div class="label"><svg width="24" height="20"><ellipse cx="10" cy="9" rx="9" ry="7" fill="none" stroke="#fff" stroke-width="2"/><path d="M5 14 3 19l6-3" fill="#fff"/></svg>On Demand<br>Meeting Rooms</div>
  </div>
  <div class="tile" style="left:145px;top:352px;width:285px;height:242px" role="img" aria-label="Presenter leading a session in a training room">
    <svg width="285" height="242"><rect width="285" height="242" fill="#6f747c"/></svg>
    <div class="label"><svg width="24" height="20"><rect x="2" y="6" width="20" height="13" rx="2" fill="#fff"/><rect x="8" y="2" width="8" height="5" fill="none" stroke="#fff" stroke-width="2"/></svg>On Demand<br>Training Rooms</div>
  </div>
  <div class="tile" style="left:456px;top:352px;width:288px;height:242px" role="img" aria-label="Laptop and documents on a wooden desk">
    <svg width="288" height="242"><rect width="288" height="242" fill="#b59a78"/></svg>
    <div class="label"><svg width="24" height="20"><rect x="2" y="5" width="12" height="14" rx="1" fill="none" stroke="#fff" stroke-width="2"/><rect x="8" y="1" width="12" height="14" rx="1" fill="none" stroke="#fff" stroke-width="2"/></svg>Virtual Office<br>Solutions</div>
  </div>
  <div class="tile" style="left:768px;top:352px;width:287px;height:242px" role="img" aria-label="Businessman on a video conference call">
    <svg width="287" height="242"><rect width="287" height="242" fill="#8b9099"/></svg>
    <div class="label"><svg width="24" height="20"><rect x="2" y="3" width="14" height="15" rx="2" fill="#fff"/><path d="M16 9l6-4v11l-6-4z" fill="#fff"/></svg>Video Conference<br>Solutions</div>
  </div>
</section>

<h2 class="abs provide-title" style="font-weight:400">What We Provide ?</h2>
<p class="abs provide-sub">We provide executive offices and virtual office services</p>

<div class="feature" style="left:140px;top:1594px">
  <div class="circle"><svg width="44" height="38"><rect x="2" y="2" width="40" height="26" rx="2" fill="none" stroke="#fff" stroke-width="4"/><rect x="17" y="29" width="10" height="5" fill="#fff"/><rect x="11" y="33" width="22" height="3" fill="#fff"/></svg></div>
  <h3>Start Ups</h3>
  <p>Flexible private suites and shared desks let young teams grow without long leases or heavy setup costs.</p>
</div>
<div class="feature" style="left:449px;top:1594px">
  <div class="circle"><svg width="42" height="42"><rect x="14" y="4" width="22" height="12" rx="2" transform="rotate(45 25 10)" fill="#fff"/><rect x="4" y="22" width="6" height="22" transform="rotate(45 7 33)" fill="#fff"/></svg></div>
  <h3>Law Firms</h3>
  <p>Polished offices, staffed reception and private meeting rooms give attorneys a trusted place to welcome every client.</p>
</div>
<div class="feature" style="left:760px;top:1594px">
  <div class="circle"><svg width="46" height="30"><rect x="2" y="2" width="42" height="26" rx="2" fill="none" stroke="#fff" stroke-width="4"/><circle cx="23" cy="15" r="7" fill="#fff"/></svg></div>
  <h3>Financial Services</h3>
  <p>Quiet executive suites, secure mail handling and conference rooms support advisors who need a refined business address.</p>
</div>

<section class="abs value">
  <h2>Value</h2>
  <p>Either you need Dallas/Ft. Worth Office Space, Dallas Executive Suites, Ft. Worth Executive Suites, Houston Office Space, Houston Executive Suites, or maybe you simply need a place to stop in and use an ondemand office or meeting room from time to time or utilize our local business phone numbers, phone answering or business addresses through one of our virtual office solutions. At Calloway, you will always find affordable and beautiful, professional properties. To make decisions easy for our full service executive suite clients, we include everything in one upfront and honest price including the office, phone answering and 55 hours of conference room time per month (alone a value of over $1,600/mo).</p>
  <div class="abs btn-outline">Learn More</div>
  <div class="abs dots"><span></span><span></span><span></span></div>
</section>

<section class="abs request">
  <svg class="abs" style="left:0;top:0" width="1200" height="560" role="img" aria-label="Businesswoman standing in a modern office behind a blue overlay">
    <defs>
      <linearGradient id="reqPhoto" x1="0" y1="0" x2="1" y2="0">
        <stop offset="0" stop-color="#3e4f86"/><stop offset=".5" stop-color="#5566a0"/><stop offset="1" stop-color="#3b4b80"/>
      </linearGradient>
    </defs>
    <rect width="1200" height="560" fill="url(#reqPhoto)"/>
  </svg>
  <h2>Request Information</h2>
  <div class="field" style="left:223px;top:122px"><label>First Name:</label><div class="input">Enter Your First Name</div></div>
  <div class="field" style="left:612px;top:122px"><label>Email:</label><div class="input">Enter Your E-mail Address</div></div>
  <div class="field" style="left:223px;top:200px"><label>Last Name:</label><div class="input">Enter Your Last Name</div></div>
  <div class="field" style="left:612px;top:200px"><label>Property Interested In:</label><div class="input">None</div></div>
  <div class="field" style="left:223px;top:278px"><label>Company Name:</label><div class="input">Enter Your Company Name</div></div>
  <div class="field" style="left:612px;top:278px"><label>Product Interested In:</label><div class="input">None</div></div>
  <div class="field" style="left:223px;top:356px;width:754px"><label>Phone Number:</label><div class="input">Executives Offices</div></div>
  <div class="abs submit">SUBMIT</div>
</section>

<footer class="abs site-footer">
  <div class="abs brand"><span class="dot"></span>Calloway</div>
  <ul class="foot-col" style="left:335px"><li>Home</li><li>Properties</li><li>Virtual Tours &amp; Videos</li><li>Photos</li><li>Broker Referrals</li></ul>
  <ul class="foot-col" style="left:562px;top:61px"><li>About Us</li><li>Contact Us</li><li>Forms</li><li>Testimonials</li><li>FAQs</li><li>Careers</li></ul>
  <ul class="foot-col" style="left:698px"><li>Furniture</li><li>Specials</li><li>Site Map</li><li>Privacy</li></ul>
  <div class="foot-contact">Dallas<span>|</span>214.555.0140<br>Houston<span>|</span>713.555.0182</div>
</footer>

<div class="abs bottom-bar">
  <span class="abs copy">© 2016 Company Name &nbsp;|&nbsp; All Rights Reserved</span>
  <span class="abs connect">Connect With Us</span>
</div>

</body>
</html>
```